Corvane Lending Partners. Professional and Established Company

A full service finance company specializing in obtaining capital for small business. Business Lending advisor, helping small business owners access the capital they need to launch, grow, or sustain their business. Many of our programs offer flexible guidelines to overcome common obstacles such as credit score, credit history, and time in business, financials, and industry type. Our streamlined funding process makes getting a business loan, business line of credit, stated income commercial real estate loan, a smooth and stress free experience.SOME OF THE MOST COMMON NEEDS FOR BUSINESS CAPITAL:• Working Capital• Debt Consolidations (loans, merchant cash advances, etc.)• Payroll• Operating Expenses• Inventory• Equipment Financing• Commercial Real Estate (Purchase, Fix & Flip, Rehab, Renovations)• Business Acquisitions• Business ExpansionWe like the websites:www.quillmorecf.com they are in the same industry and provide the same servicesWe are wanting to be able to update when we do press releases and such using Word Press. Our look should be very professional and we will be adding Our Team Professional Bios and Headshots.

Industry/Entity Type

Finance

Number of Pages Required

5+ page

Font styles to use
Serif
Sans Serif

Requirements
Must have
• We want to copy quillmorecf.com
• We need:
• Home Page
• About Us
• Loan Programs
• Loan Criteria
• News
• Apply Now
• Contact
Nice to have
• See quillmorecf.com
Should not have
• Need professional design. Nothing bright or abstract

```html
<!DOCTYPE html>
<html lang="en">
<head>
<meta charset="utf-8">
<title>Corvane Lending Partners</title>
<link href="https://fonts.googleapis.com/css2?family=Cinzel:wght@400;700&family=Open+Sans:wght@400;600;700&display=swap" rel="stylesheet">
<style>
:root{
  --blue:#2a73b8;
  --blue-dark:#1f5f9e;
  --green:#6fae2a;
  --ink:#333;
  --muted:#555;
  --line:#d9d9d9;
  --white:#fff;
}
*{margin:0;padding:0;box-sizing:border-box}
html,body{width:1200px;height:4000px;overflow:hidden}
body{position:relative;background:var(--white);font-family:"Open Sans",Arial,sans-serif;color:var(--ink)}
.abs{position:absolute}

/* header */
.brand{left:147px;top:32px;font-family:"Cinzel",Georgia,serif;font-size:24px;font-weight:700;color:var(--blue);display:flex;align-items:center;gap:10px;white-space:nowrap}
.brand-dot{width:13px;height:13px;background:var(--blue)}
.contact{top:32px;right:140px;display:flex;gap:50px;font-size:14px;color:var(--ink)}
.contact span{display:flex;align-items:center;gap:10px}
.nav{top:74px;right:140px;display:flex;gap:20px;font-size:13.5px;text-transform:uppercase;color:var(--ink)}

/* hero */
.hero{left:0;top:120px;width:1200px;height:520px;background:linear-gradient(110deg,#2b2a28 0%,#5a4d3e 45%,#b58f62 70%,#e7d6c0 100%)}
.hero-sub{left:147px;top:250px;color:#fff;font-size:17px;font-weight:600}
.hero-title{left:147px;top:288px;color:#fff;font-family:"Cinzel",Georgia,serif;font-size:40px;line-height:62px;font-weight:700;letter-spacing:1px}
.btn-solid{left:147px;top:432px;width:168px;height:48px;background:var(--blue);border:2px solid #fff;color:#fff;font-size:16px;font-weight:600;display:flex;align-items:center;justify-content:center;text-transform:uppercase}
.arrow{color:#fff;font-size:38px}

/* section headings */
.sec-rule{width:110px;height:2px;background:var(--blue)}
.sec-title{width:1200px;left:0;text-align:center;font-family:"Cinzel",Georgia,serif;font-size:30px;font-weight:400;color:var(--ink)}

/* loans */
.loans{left:147px;top:813px;width:912px;height:134px;display:flex}
.loan{flex:1;text-align:center;border-left:1px solid var(--line);padding-top:16px}
.loan:last-child{border-right:1px solid var(--line)}
.loan-type{font-size:13px;color:var(--muted)}
.loan-amt{font-size:19px;color:var(--green);font-weight:600;margin:12px 0 10px}
.loan-meta{font-size:11px;color:var(--muted);line-height:17px}

/* feature bands */
.band{background:var(--blue)}
.band-copy{width:410px;display:flex;flex-direction:column;align-items:flex-start;color:#fff}
.band-rule{width:110px;height:2px;background:#fff;margin-left:30px}
.band-title{font-family:"Cinzel",Georgia,serif;font-size:28px;font-weight:400;color:#fff;margin-top:6px;line-height:38px}
.band-text{font-size:12px;line-height:27px;color:#fff;margin-top:10px}
.btn-line{margin-top:26px;width:134px;height:44px;border:2px solid #fff;color:#fff;font-size:14px;font-weight:700;display:flex;align-items:center;justify-content:center;text-transform:uppercase}
.photo{border:6px solid #fff;box-shadow:0 2px 8px rgba(0,0,0,.15)}

/* services */
.svc{width:296px;text-align:center}
.svc-img{width:296px;height:200px}
.svc-name{margin-top:30px;font-size:17px;font-weight:600;text-transform:uppercase;color:var(--ink)}
.svc-text{margin-top:10px;font-size:13px;line-height:26px;color:var(--muted)}

/* team */
.team{left:0;top:3312px;width:1200px;height:528px;background:linear-gradient(90deg,#eceef1 0%,#f3eef0 60%,#f6e9ec 100%)}
.team-intro{left:0;width:1200px;top:3422px;text-align:center;font-size:13.5px;line-height:27px;color:var(--muted)}
.member{width:220px;text-align:center}
.avatar{width:122px;height:122px;border-radius:50%;border:4px solid #fff;margin:0 auto;box-shadow:0 1px 4px rgba(0,0,0,.15)}
.member-name{margin-top:22px;font-size:15px;font-weight:700;color:var(--blue)}
.member-bio{margin-top:6px;font-size:13px;line-height:24px;color:var(--muted)}
.team-arrow{font-size:28px;color:var(--ink)}

/* footer */
.footer{left:0;top:3840px;width:1200px;height:160px;background:var(--blue)}
.foot-nav{left:0;width:1200px;top:3878px;display:flex;justify-content:center;gap:30px;color:#fff;font-size:15px}
.foot-rule{left:147px;top:3926px;width:906px;height:1px;background:rgba(255,255,255,.45)}
.copy{left:140px;top:3960px;color:#fff;font-size:13px}
.social{left:910px;top:3950px;display:flex;gap:12px}
.social span{width:26px;height:26px;border:1.5px solid #fff;border-radius:50%}
</style>
</head>
<body>

<!-- header -->
<div class="abs brand"><span class="brand-dot"></span>Corvane Lending Partners</div>
<div class="abs contact">
  <span><svg width="14" height="14" viewBox="0 0 24 24"><path fill="#2a73b8" d="M6.6 10.8a15.1 15.1 0 0 0 6.6 6.6l2.2-2.2c.3-.3.7-.4 1-.2 1.1.4 2.3.6 3.6.6.6 0 1 .4 1 1V20c0 .6-.4 1-1 1A17 17 0 0 1 3 4c0-.6.4-1 1-1h3.5c.6 0 1 .4 1 1 0 1.2.2 2.4.6 3.6.1.3 0 .7-.2 1z"/></svg>(+1) 555 014 2270</span>
  <span><svg width="16" height="12" viewBox="0 0 16 12"><rect width="16" height="12" fill="#2a73b8"/><path d="M0 0l8 6 8-6" stroke="#fff" fill="none"/></svg>info@corvanelending.com</span>
</div>
<nav class="abs nav"><span>Home</span><span>About Us</span><span>Loan Programs</span><span>Loan Criteria</span><span>News</span><span>Apply Now</span><span>Contact</span></nav>

<!-- hero -->
<div class="abs hero" role="img" aria-label="Hands reviewing financial documents with a pen and tablet"></div>
<div class="abs hero-sub">Specializing in obtaining capital for small business</div>
<h1 class="abs hero-title">WE ARE A FULL SERVICE<br>FINANCE COMPANY</h1>
<div class="abs btn-solid">Get Started</div>
<div class="abs arrow" style="left:56px;top:360px">&laquo;</div>
<div class="abs arrow" style="left:1120px;top:360px">&raquo;</div>

<!-- recently closed loans -->
<div class="abs sec-rule" style="left:545px;top:735px"></div>
<h2 class="abs sec-title" style="top:758px">RECENTLY CLOSED LOANS</h2>
<div class="abs loans">
  <div class="loan"><div class="loan-type">Retail Development</div><div class="loan-amt">$12,500,200</div><div class="loan-meta">Refinance<br>New York, New York</div></div>
  <div class="loan"><div class="loan-type">Mixed Use</div><div class="loan-amt">$12,500,200</div><div class="loan-meta">Land Acquisition<br>Miami, FL</div></div>
  <div class="loan"><div class="loan-type">Two Hotels</div><div class="loan-amt">$12,500,200</div><div class="loan-meta">Refinancing<br>Jersey City, NJ</div></div>
  <div class="loan"><div class="loan-type">Condominium</div><div class="loan-amt">$12,500,200</div><div class="loan-meta">Land Acquisition<br>Mansfield, Texas</div></div>
  <div class="loan"><div class="loan-type">Mixed Use</div><div class="loan-amt">$12,500,200</div><div class="loan-meta">Cash Out<br>Chicago, IL</div></div>
</div>

<!-- who we are -->
<div class="abs band" style="left:0;top:1040px;width:637px;height:429px"></div>
<div class="abs band-copy" style="left:147px;top:1100px">
  <div class="band-rule"></div>
  <h2 class="band-title">WHO WE ARE</h2>
  <p class="band-text">Lorem Ipsum. Proin gravida nibh vel velit auctor aliquet. Aenean sollicitudin, sum, nec sagittis sem nibh id elit. Duis sed odio sit amet nibh vulputate cursus auctor a ornare odio sit amet.</p>
  <p class="band-text">Lorem Ipsum. Proin gravida nibh vel velit auctor aliquet. Aenean sollicit sed odio, ipsum, nec sagittis sem nibh id elit vulputate cursus.</p>
  <div class="btn-line">Read More</div>
</div>
<div class="abs photo" style="left:595px;top:1085px;width:464px;height:334px;background:linear-gradient(135deg,#e9ecef,#b9c3cc 50%,#8e98a3)" role="img" aria-label="Hands using a calculator over financial papers"></div>

<!-- recent news -->
<div class="abs band" style="left:536px;top:1565px;width:664px;height:430px"></div>
<div class="abs photo" style="left:147px;top:1613px;width:461px;height:334px;background:linear-gradient(180deg,#7fb2e0 0%,#c7dcee 40%,#6f8f7a 70%,#a9a9a6 100%)" role="img" aria-label="Modern glass office building with trees in front"></div>
<div class="abs band-copy" style="left:672px;top:1625px">
  <div class="band-rule" style="margin-left:88px"></div>
  <h2 class="band-title">RECENT NEWS</h2>
  <p class="band-text">Lorem Ipsum. Proin gravida nibh vel velit auctor aliquet. Aenean sollicitudin, sum, nec sagittis sem nibh id elit. Duis sed odio sit amet nibh vulputate cursus auctor a ornare odio sit amet.</p>
  <p class="band-text">Lorem Ipsum. Proin gravida nibh vel velit auctor aliquet. Aenean sollicit sed odio, ipsum, nec sagittis sem nibh id elit vulputate cursus.</p>
  <div class="btn-line">Read More</div>
</div>

<!-- our services -->
<div class="abs sec-rule" style="left:545px;top:2110px"></div>
<h2 class="abs sec-title" style="top:2128px">OUR SERVICES</h2>

<div class="abs svc" style="left:147px;top:2205px"><div class="svc-img" role="img" aria-label="Business people reviewing charts" style="background:linear-gradient(135deg,#c9b08c,#e9e6e0 50%,#7f8ea0)"></div><div class="svc-name">Working Capital</div><div class="svc-text">Lorem Ipsum is simply dummy text of<br>printing ever since 1500s</div></div>
<div class="abs svc" style="left:451px;top:2205px"><div class="svc-img" role="img" aria-label="Two women in a consultation meeting" style="background:linear-gradient(135deg,#d7b59a,#f0e6dc 50%,#9c7a68)"></div><div class="svc-name">Debt Consolidations</div><div class="svc-text">Lorem Ipsum is simply dummy text of<br>printing ever since 1500s</div></div>
<div class="abs svc" style="left:757px;top:2205px"><div class="svc-img" role="img" aria-label="Hand passing a check across a desk" style="background:linear-gradient(135deg,#5a4035,#a07a63 50%,#e6ddd3)"></div><div class="svc-name">Payroll</div><div class="svc-text">Lorem Ipsum is simply dummy text of<br>printing ever since 1500s</div></div>

<div class="abs svc" style="left:147px;top:2563px"><div class="svc-img" role="img" aria-label="Calculator and pen on financial statements" style="background:linear-gradient(135deg,#8c8f93,#d8d5cf 50%,#c39a6b)"></div><div class="svc-name">Operating Expenses</div><div class="svc-text">Lorem Ipsum is simply dummy text of<br>printing ever since 1500s</div></div>
<div class="abs svc" style="left:451px;top:2563px"><div class="svc-img" role="img" aria-label="Tablet showing an inventory spreadsheet" style="background:linear-gradient(135deg,#6a2f2b,#b0715c 50%,#d9c3a4)"></div><div class="svc-name">Inventory</div><div class="svc-text">Lorem Ipsum is simply dummy text of<br>printing ever since 1500s</div></div>
<div class="abs svc" style="left:757px;top:2563px"><div class="svc-img" role="img" aria-label="Farm worker standing beside a red tractor" style="background:linear-gradient(135deg,#d9e0e6,#9d3a30 45%,#5b6e86)"></div><div class="svc-name">Equipment Financing</div><div class="svc-text">Lorem Ipsum is simply dummy text of<br>printing ever since 1500s</div></div>

<div class="abs svc" style="left:147px;top:2917px"><div class="svc-img" role="img" aria-label="Glass commercial office towers" style="background:linear-gradient(180deg,#9cb7d1,#4f6a83 60%,#8a8a86)"></div><div class="svc-name">Commercial Real Estate</div><div class="svc-text">Lorem Ipsum is simply dummy text of<br>printing ever since 1500s</div></div>
<div class="abs svc" style="left:451px;top:2917px"><div class="svc-img" role="img" aria-label="Business handshake over documents" style="background:linear-gradient(135deg,#2f3840,#7f8a94 50%,#d2d6da)"></div><div class="svc-name">Business Acquisitions</div><div class="svc-text">Lorem Ipsum is simply dummy text of<br>printing ever since 1500s</div></div>
<div class="abs svc" style="left:757px;top:2917px"><div class="svc-img" role="img" aria-label="Team working with laptops around a wooden table" style="background:linear-gradient(135deg,#5d4a3b,#9a8270 50%,#e4e0da)"></div><div class="svc-name">Business Expansion</div><div class="svc-text">Lorem Ipsum is simply dummy text of<br>printing ever since 1500s</div></div>

<!-- our team -->
<div class="abs team"></div>
<h2 class="abs sec-title" style="top:3372px">OUR TEAM</h2>
<p class="abs team-intro">Lorem ipsum dolormet, consectetur adipisicingelit, sedo eiumod tempor incidiunto laborent dolore magna.<br>aliqua enimminim veniam, quis nostrrua bonual lamco laborist alimodo consequat.</p>
<div class="abs team-arrow" style="left:60px;top:3582px">&laquo;</div>
<div class="abs team-arrow" style="left:1124px;top:3582px">&raquo;</div>
<div class="abs member" style="left:250px;top:3515px"><div class="avatar" role="img" aria-label="Headshot of team member" style="background:linear-gradient(135deg,#d8c1a8,#9c7c62)"></div><div class="member-name">Dana Whitlow</div><div class="member-bio">Sed uta perspiciatis<br>unde omnis isteua natus<br>eaque sit voluptat.</div></div>
<div class="abs member" style="left:490px;top:3515px"><div class="avatar" role="img" aria-label="Headshot of team member" style="background:linear-gradient(135deg,#c9b39d,#7d6857)"></div><div class="member-name">Marcus Hale</div><div class="member-bio">Sed uta perspiciatis<br>unde omnis isteua natus<br>eaque sit voluptat.</div></div>
<div class="abs member" style="left:730px;top:3515px"><div class="avatar" role="img" aria-label="Headshot of team member" style="background:linear-gradient(135deg,#cdbfb3,#5e4638)"></div><div class="member-name">Nadia Orren</div><div class="member-bio">Sed uta perspiciatis<br>unde omnis isteua natus<br>eaque sit voluptat.</div></div>

<!-- footer -->
<div class="abs footer"></div>
<nav class="abs foot-nav"><span>Home</span><span>About Us</span><span>Loan Programs</span><span>Loan Criteria</span><span>News</span><span>Apply Now</span><span>Contact</span></nav>
<div class="abs foot-rule"></div>
<div class="abs copy">Copyright &copy; 2018. All Rights Reserved.</div>
<div class="abs social"><span></span><span></span><span></span><span></span></div>

</body>
</html>
```